Create a flyer for our party getaway to Ibiza.

'The Drifted Ibiza Getaway'

Friday 14th July - Monday 17th July

DJ Varro & DJ Mercer brings together a jam-packed weekend schedule full of the best urban parties in Ibiza.

What's included?

4 Nights Of Entertainment
6 Parties In Total
1 Boat Party
1 Pool Party
2 Superclub Parties
1 Indoor Water Party
Bottomless Drinks (Boat Party Only)
An unbelievable experience
1 unbeatable price.

All this for 140€ (you save 50€ when you book with us)

Tickets avaialble from Tixlane & Gobrino

Target Market(s)

holiday goers

Industry/Entity Type

party, events, club, hip hop

Requirements
Must have
• good vibes
Nice to have
• nice catchy looking title

```html
<!DOCTYPE html>
<html lang="en">
<head>
<meta charset="utf-8">
<title>The Drifted Ibiza Getaway</title>
<link href="https://fonts.googleapis.com/css2?family=Anton&family=Archivo+Black&family=Bebas+Neue&family=Kaushan+Script&family=Montserrat:wght@500;600;700;800&display=swap" rel="stylesheet">
<style>
  :root {
    --navy: #030a1f;
    --deep: #0b1033;
    --purple: #5a2fa8;
    --violet: #7a3cc8;
    --blue: #2a5fd8;
    --cyan: #27dcf5;
    --cyan-deep: #0a74b8;
    --pink: #f2119b;
    --orange: #f7861f;
    --white: #ffffff;
    --text-soft: #e8ecf7;
  }
  * { box-sizing: border-box; margin: 0; padding: 0; }
  html, body { width: 809px; height: 1200px; overflow: hidden; background: #dddddd; }
  .flyer {
    position: relative;
    width: 809px; height: 1200px; overflow: hidden;
    background:
      radial-gradient(ellipse 60% 22% at 0% 58%, rgba(39,220,245,.35), transparent 70%),
      radial-gradient(ellipse 60% 22% at 100% 58%, rgba(242,17,155,.35), transparent 70%),
      radial-gradient(ellipse 90% 35% at 50% 55%, rgba(122,60,200,.55), transparent 75%),
      linear-gradient(180deg, var(--deep) 0%, #231a5c 40%, #1a1244 62%, var(--navy) 76%, var(--navy) 100%);
    font-family: "Montserrat", sans-serif;
    color: var(--white);
  }
  .hero-photo {
    position: absolute; left: 0; top: 0; width: 809px; height: 440px;
    background:
      radial-gradient(ellipse 40% 45% at 38% 55%, rgba(230,225,245,.55), transparent 70%),
      radial-gradient(ellipse 35% 45% at 62% 60%, rgba(235,225,240,.5), transparent 70%),
      radial-gradient(ellipse 30% 50% at 88% 45%, rgba(150,120,230,.45), transparent 70%),
      linear-gradient(180deg, #1f3fb8 0%, #3b2f9e 45%, #4a2a96 80%, rgba(40,25,100,0) 100%);
  }
  .title-pill {
    position: absolute; left: 167px; top: 431px; width: 475px; height: 70px;
    border: 2px solid var(--white); border-radius: 22px;
    background: var(--navy);
    padding: 7px 18px;
  }
  .title-pill span {
    display: block; height: 100%; border-radius: 14px;
    background: linear-gradient(90deg, var(--pink) 0%, var(--pink) 55%, #5a1a6e 100%);
    font-family: "Archivo Black", sans-serif; font-size: 38px; letter-spacing: 11px;
    line-height: 52px; text-align: center; color: var(--white); padding-left: 10px;
    white-space: nowrap;
  }
  .title-ibiza {
    position: absolute; left: 0; width: 809px; top: 500px; text-align: center;
    font-family: "Anton", sans-serif; font-size: 190px; line-height: 190px; letter-spacing: 2px;
    font-weight: 400;
    transform: scaleX(1.28);
    background: linear-gradient(180deg, #6ff0ff 0%, var(--cyan) 45%, var(--cyan-deep) 60%, #2fb6e8 100%);
    -webkit-background-clip: text; background-clip: text; color: transparent;
    filter: drop-shadow(4px 4px 0 #ff5a4a) drop-shadow(0 0 14px rgba(39,220,245,.45));
  }
  .title-getaway {
    position: absolute; left: 0; width: 809px; top: 640px; text-align: center;
    font-family: "Kaushan Script", cursive; font-size: 108px; line-height: 140px;
    color: var(--white); transform: rotate(-4deg);
    text-shadow: 0 0 4px var(--pink), 0 0 16px var(--pink), 3px 4px 0 #7a0a55;
  }
  .dates {
    position: absolute; left: 0; width: 809px; top: 806px; text-align: center;
    font-family: "Bebas Neue", sans-serif; font-size: 56px; line-height: 56px; letter-spacing: .5px;
    white-space: nowrap;
  }
  .dates .pink { color: var(--pink); }
  .dates .cyan { color: var(--cyan); }
  .dates sup { font-size: 26px; vertical-align: 22px; line-height: 0; }
  .rule {
    position: absolute; left: 95px; width: 620px; height: 0;
    border-top: 2px dotted rgba(255,255,255,.35);
  }
  .djs {
    position: absolute; left: 0; width: 809px; top: 874px; text-align: center;
    font-family: "Archivo Black", sans-serif; font-size: 42px; line-height: 50px; letter-spacing: 1px;
    font-weight: 400; white-space: nowrap;
  }
  .intro {
    position: absolute; left: 0; width: 809px; top: 925px; text-align: center;
    font-size: 15.5px; font-weight: 600; line-height: 20px; color: var(--text-soft);
  }
  .intro em { font-style: normal; color: var(--cyan); font-weight: 700; }
  .inclusions {
    position: absolute; left: 52px; top: 989px; width: 705px; height: 40px;
    display: flex; align-items: center; justify-content: space-between;
    list-style: none;
  }
  .inclusion { display: flex; align-items: center; gap: 6px; padding-right: 8px; border-right: 1px solid rgba(39,220,245,.45); height: 40px; white-space: nowrap; }
  .inclusion:last-child { border-right: 0; padding-right: 0; }
  .inclusion b { font-size: 36px; font-weight: 500; color: var(--orange); line-height: 1; }
  .inclusion span { font-size: 11.5px; font-weight: 500; line-height: 17px; text-transform: uppercase; }
  .perk {
    position: absolute; top: 1049px; height: 31px;
    border: 2px solid var(--pink); border-radius: 8px;
    font-size: 11.5px; font-weight: 500; line-height: 27px; text-transform: uppercase;
    text-align: center; white-space: nowrap;
  }
  .perk.drinks { left: 53px; width: 318px; }
  .perk.experience { left: 379px; width: 221px; }
  .perk.price-tag { left: 608px; width: 150px; }
  .price-label {
    position: absolute; left: 104px; top: 1090px;
    font-size: 16px; font-weight: 600; line-height: 20px; color: var(--pink); text-transform: uppercase;
    white-space: nowrap;
  }
  .price {
    position: absolute; left: 108px; top: 1104px;
    font-family: "Archivo Black", sans-serif; font-size: 54px; line-height: 60px; color: var(--cyan);
    white-space: nowrap;
  }
  .saving {
    position: absolute; left: 261px; top: 1119px;
    font-size: 13px; font-weight: 500; line-height: 17px; text-transform: uppercase;
    white-space: nowrap;
  }
  .divider { position: absolute; left: 432px; top: 1092px; width: 2px; height: 66px; background: var(--orange); }
  .tickets-label {
    position: absolute; left: 455px; top: 1096px;
    font-size: 16px; font-weight: 600; line-height: 20px; letter-spacing: .3px; text-transform: uppercase;
    white-space: nowrap;
  }
  .sellers { position: absolute; left: 455px; top: 1126px; display: flex; gap: 20px; align-items: center; }
  .seller { display: flex; align-items: center; gap: 7px; font-size: 21px; font-weight: 800; line-height: 30px; white-space: nowrap; }
  .seller i { display: block; width: 12px; height: 12px; }
  .seller.gobrino { color: var(--white); }
  .seller.gobrino i { background: var(--white); }
  .seller.tixlane { color: var(--orange); }
  .seller.tixlane i { background: var(--orange); }
</style>
</head>
<body>
  <main class="flyer">
    <div class="hero-photo" role="img" aria-label="Photo of the two DJs posing in white T-shirts beside a DJ booth, with blue and purple stage lighting"></div>

    <div class="title-pill"><span>THE DRIFTED</span></div>
    <h1 class="title-ibiza">IBIZA</h1>
    <div class="title-getaway">Getaway</div>

    <p class="dates">
      <span class="pink">Friday</span> <span class="cyan">14<sup>th</sup> July</span> to
      <span class="pink">Monday</span> <span class="cyan">17<sup>th</sup> July</span>
    </p>
    <div class="rule" style="top:868px"></div>

    <h2 class="djs">DJ VARRO &amp; DJ MERCER</h2>
    <p class="intro">brings together a jam-packed weekend schedule full<br>of the best urban parties <em>in Ibiza</em></p>
    <div class="rule" style="top:978px"></div>

    <ul class="inclusions">
      <li class="inclusion"><b>4</b><span>Nights of<br>entertainment</span></li>
      <li class="inclusion"><b>6</b><span>Parties<br>in total</span></li>
      <li class="inclusion"><b>1</b><span>Boat<br>party</span></li>
      <li class="inclusion"><b>1</b><span>Pool<br>party</span></li>
      <li class="inclusion"><b>2</b><span>Superclub<br>parties</span></li>
      <li class="inclusion"><b>1</b><span>Indoor<br>water party</span></li>
      <li class="inclusion"><b>1</b><span>Beach<br>day</span></li>
    </ul>
    <div class="rule" style="top:1040px"></div>

    <span class="perk drinks">Bottomless drinks (pre boat party only)</span>
    <span class="perk experience">An unbelievable experience</span>
    <span class="perk price-tag">1 unbeatable price</span>

    <p class="price-label">All this for</p>
    <p class="price">140€</p>
    <p class="saving">You save 50€ when<br>you book with us</p>

    <div class="divider"></div>
    <p class="tickets-label">Tickets avaialble from</p>
    <div class="sellers">
      <span class="seller gobrino"><i></i>Gobrino</span>
      <span class="seller tixlane"><i></i>Tixlane</span>
    </div>
  </main>
</body>
</html>
```